Commercial Waterproofing Modern Business Cards

We are a Commercial Waterproofing company. We do a variety of jobs on the exterior of buildings. We repel from the top or scaffold to reach the areas. Cut out and recaulk expansion joints and apply sealants, brick/concrete repairs, seal window frame perimeters, and much more. Our website is www.tallwallmend.com.
We are looking for a new business card design that would look more modern and cutting edge. We like the transparent paper and had thought about using our logo, but maybe pulling it apart to where the building part is kind of in the background. I have attached 2 different logos that we use regularly. We want the design to be a little funky, but professional at the same time. We really don't want the logo to be incorporated by itself, but you can use the logo and take out the buildings and just use the name or vice versa. Please don't just put the logo on the card and the words around that.

Target Market(s)

Property Managers/Building Maintenance

Industry/Entity Type

Business

Contact Information for Business Card

Dorian Vellstrom President
Office (555)418-2097
Mobile (555)604-7351

Font styles to use
Serif

Requirements
Must have
• Nice overall design, somehow pulling from the logo for the design
Nice to have
• Look artsy and modern with a nice quality paper
Should not have
• Too many words or distracting designs. The logo 'as is'

```html
<!DOCTYPE html>
<html lang="en">
<head>
<meta charset="utf-8">
<title>TallWall Mend Business Card</title>
<link href="https://fonts.googleapis.com/css2?family=Montserrat:wght@400;500&display=swap" rel="stylesheet">
<style>
  :root {
    --page: #2a2a2c;
    --card-light: #3a64a3;
    --card-mid: #2b5390;
    --card-dark: #1f3f74;
    --panel: #3b679f;
    --white: #f4f6fa;
    --accent: #27a6dc;
    --divider: rgba(255,255,255,0.85);
    --arc: rgba(255,255,255,0.07);
  }
  html, body {
    margin: 0;
    width: 1200px;
    height: 800px;
    overflow: hidden;
    background: var(--page);
    font-family: "Montserrat", sans-serif;
  }
  .card {
    position: absolute;
    left: 75px;
    top: 100px;
    width: 1050px;
    height: 600px;
    border-radius: 44px;
    overflow: hidden;
    background: radial-gradient(ellipse at 62% 50%, var(--card-light) 0%, var(--card-mid) 45%, var(--card-dark) 100%);
    box-shadow: 0 6px 0 #1a3566, 0 12px 0 #16305c, 0 24px 40px rgba(0,0,0,0.45);
  }
  .card__arcs {
    position: absolute;
    inset: 0;
  }
  .brand-panel {
    position: absolute;
    left: 70px;
    top: 235px;
    width: 510px;
    height: 190px;
    background: linear-gradient(90deg, #46709f 0%, var(--panel) 60%, #356299 100%);
    display: flex;
    align-items: center;
    justify-content: center;
    gap: 16px;
  }
  .brand-panel__dot {
    width: 22px;
    height: 22px;
    border-radius: 50%;
    background: var(--white);
  }
  .brand-panel__name {
    color: var(--white);
    font-weight: 500;
    font-size: 40px;
    letter-spacing: 1px;
  }
  .divider {
    position: absolute;
    left: 620px;
    top: 150px;
    width: 2px;
    height: 320px;
    background: linear-gradient(180deg, transparent, var(--divider) 20%, var(--divider) 80%, transparent);
  }
  .person {
    position: absolute;
    right: 90px;
    top: 70px;
    text-align: right;
  }
  .person__name {
    color: var(--white);
    font-weight: 500;
    font-size: 34px;
    letter-spacing: 1.5px;
    margin: 0;
  }
  .person__title {
    color: var(--accent);
    font-size: 28px;
    letter-spacing: 2px;
    margin: 2px 0 0;
  }
  .contacts {
    position: absolute;
    right: 70px;
    top: 280px;
    list-style: none;
    margin: 0;
    padding: 0;
    text-align: right;
  }
  .contacts__item {
    display: flex;
    align-items: center;
    justify-content: flex-end;
    gap: 20px;
    height: 70px;
    color: var(--white);
    font-size: 28px;
    letter-spacing: 2px;
  }
  .contacts__item--web { font-size: 26px; }
  .contacts__icon { width: 46px; height: 46px; flex: none; }
</style>
</head>
<body>
  <div class="card">
    <svg class="card__arcs" viewBox="0 0 1050 600" aria-hidden="true">
      <path d="M-50 520 Q 400 120 1100 180" fill="none" stroke="var(--arc)" stroke-width="2"/>
      <path d="M150 -20 Q 450 300 300 640" fill="none" stroke="var(--arc)" stroke-width="2"/>
      <path d="M680 -20 Q 560 300 880 640" fill="none" stroke="var(--arc)" stroke-width="2"/>
      <path d="M1080 80 Q 700 350 420 640" fill="none" stroke="var(--arc)" stroke-width="2"/>
    </svg>

    <div class="brand-panel" role="img" aria-label="Soft-toned city skyline artwork behind the company name">
      <span class="brand-panel__dot"></span>
      <span class="brand-panel__name">TallWall Mend</span>
    </div>

    <div class="divider"></div>

    <div class="person">
      <p class="person__name">Dorian Vellstrom</p>
      <p class="person__title">President</p>
    </div>

    <ul class="contacts">
      <li class="contacts__item">(555)418-2097
        <svg class="contacts__icon" viewBox="0 0 46 46" aria-hidden="true">
          <polygon points="23,2 44,17 36,43 10,43 2,17" fill="var(--accent)"/>
          <path d="M16 15 l4 -2 l3 6 l-2 2 q2 4 5 6 l2 -2 l6 3 l-2 4 q-8 1 -16 -11 z" fill="var(--white)"/>
        </svg>
      </li>
      <li class="contacts__item">(555)604-7351
        <svg class="contacts__icon" viewBox="0 0 46 46" aria-hidden="true">
          <polygon points="23,2 44,17 36,43 10,43 2,17" fill="var(--accent)"/>
          <rect x="17" y="12" width="12" height="22" rx="2" fill="none" stroke="var(--white)" stroke-width="2"/>
          <circle cx="23" cy="30" r="1.3" fill="var(--white)"/>
        </svg>
      </li>
      <li class="contacts__item contacts__item--web">www.tallwallmend.com
        <svg class="contacts__icon" viewBox="0 0 46 46" aria-hidden="true">
          <polygon points="23,2 44,17 36,43 10,43 2,17" fill="var(--accent)"/>
          <rect x="12" y="14" width="22" height="14" rx="1.5" fill="none" stroke="var(--white)" stroke-width="2"/>
          <path d="M19 33 h8 M23 28 v5" stroke="var(--white)" stroke-width="2"/>
        </svg>
      </li>
    </ul>
  </div>
</body>
</html>
```